5 website banners (slides show)

We need 5 website sliding banners created for a website all about internet safety. The topics for each banner are:

Cyberbullying
Fraud
seniors
social networking

Sizes: 953 pixels x 281 pixels

I have stock images to use or feel free to use your own or one I can purchase from pixelharbor.example.

Industry/Entity Type

Internet

```html
<!DOCTYPE html>
<html lang="en">
<head>
<meta charset="utf-8">
<title>Netwise – Online Safety and Security</title>
<link href="https://fonts.googleapis.com/css2?family=Ubuntu:wght@400;500;700&family=Fredoka:wght@600&family=Arimo:wght@400;700&display=swap" rel="stylesheet">
<style>
  :root {
    --pink: #ff0090;
    --pink-deep: #e6007f;
    --green: #55bf13;
    --green-dark: #3f9e0a;
    --green-light: #6fd42a;
    --text-grey: #7f8f96;
    --white: #ffffff;
    --page: #ffffff;
  }
  * { box-sizing: border-box; margin: 0; padding: 0; }
  html, body { width: 1200px; height: 1158px; overflow: hidden; background: var(--page); }
  body { position: relative; font-family: "Arimo", Arial, sans-serif; }

  .utility-bar {
    position: absolute; left: 42px; top: 27px; width: 1116px; height: 39px;
    background: var(--pink); border-radius: 5px 0 0 5px;
  }
  .utility-links { position: absolute; left: 18px; top: 11px; display: flex; gap: 30px; }
  .utility-links a { color: var(--white); text-decoration: none; font-size: 15px; }
  .social-square { position: absolute; left: 718px; top: 7px; width: 28px; height: 28px; background: #1a4f8f; border-radius: 3px; }
  .search-field {
    position: absolute; left: 752px; top: 2px; width: 322px; height: 35px;
    background: var(--white); border: 1px solid #e0e6ea; color: #9aa6ad;
    font-size: 15px; padding: 9px 10px;
  }
  .search-button { position: absolute; left: 1081px; top: 4px; width: 32px; height: 32px; background: var(--pink); border: 2px solid #fff; border-radius: 4px; }

  .brand { position: absolute; left: 61px; top: 84px; }
  .brand-circle { position: absolute; left: 0; top: 0; width: 115px; height: 115px; border-radius: 50%; background: var(--pink); }
  .brand-name {
    position: absolute; left: 134px; top: 14px; font-family: "Ubuntu", sans-serif; font-weight: 500;
    font-size: 70px; color: var(--pink); line-height: 1; white-space: nowrap;
  }
  .brand-tagline {
    position: absolute; left: 137px; top: 83px; font-family: "Ubuntu", sans-serif; font-size: 17px;
    color: var(--green-dark); white-space: nowrap;
  }

  .report-box {
    position: absolute; left: 741px; top: 93px; width: 419px; height: 113px;
    background: linear-gradient(180deg, #7ad92c, #4fb70e); border-radius: 4px;
    border: 1px dashed rgba(255,255,255,.5);
  }
  .report-title { position: absolute; left: 20px; top: 16px; font-family: "Ubuntu", sans-serif; font-weight: 700; font-size: 25px; color: var(--white); white-space: nowrap; }
  .report-click { position: absolute; left: 218px; top: 47px; font-family: "Ubuntu", sans-serif; font-size: 16px; color: var(--white); white-space: nowrap; }
  .report-phone { position: absolute; left: 18px; top: 66px; font-family: "Ubuntu", sans-serif; font-weight: 700; font-size: 29px; color: var(--white); white-space: nowrap; }
  .report-shield { position: absolute; right: 16px; top: 8px; }

  .main-nav {
    position: absolute; left: 42px; top: 227px; width: 1118px; height: 79px;
    background: var(--green-dark); border-radius: 5px;
  }
  .main-nav ul { list-style: none; display: flex; height: 64px; background: var(--green); border-radius: 5px 5px 0 0; }
  .main-nav li {
    flex: none; font-family: "Ubuntu", sans-serif; font-size: 18px; color: var(--white);
    text-align: center; white-space: nowrap; line-height: 64px;
    border-right: 2px solid rgba(255,255,255,.35);
  }
  .main-nav li.current { background: var(--green-light); border-radius: 5px 0 0 0; }
  .nav-home { width: 94px; }
  .nav-about { width: 101px; }
  .nav-parents { width: 158px; }
  .nav-teens { width: 137px; }
  .nav-tweens { width: 157px; }
  .nav-kids { width: 118px; }
  .nav-teachers { width: 170px; }
  .nav-resources { width: 143px; }

  .hero {
    position: absolute; left: 42px; top: 319px; width: 1121px; height: 330px;
    background: linear-gradient(180deg, #ff1aa0, var(--pink-deep)); border-radius: 5px; overflow: hidden;
  }
  .hero-photo {
    position: absolute; left: -96px; top: -60px; width: 520px; height: 460px; border-radius: 50%;
    background: radial-gradient(circle at 55% 45%, #e9d7d2, #a9a5a7 60%, #5f5d62);
    border: 14px solid #1cae2e;
  }
  .hero-character { position: absolute; left: 410px; top: 88px; width: 170px; height: 242px; border-radius: 40px; background: linear-gradient(180deg, #9de03a, #2f9a3a); }
  .hero-title {
    position: absolute; left: 610px; top: 132px; font-family: "Fredoka", sans-serif; font-weight: 600;
    font-size: 54px; line-height: 1; color: var(--white); white-space: nowrap;
  }

  .issue-sidebar {
    position: absolute; left: 42px; top: 661px; width: 259px; height: 520px;
    background: var(--green-light); border-radius: 6px;
  }
  .issue-frame { position: absolute; left: 12px; top: 12px; right: 12px; bottom: 30px; border: 1px dashed rgba(255,255,255,.8); border-radius: 6px; }
  .issue-heading { position: absolute; left: 25px; top: 36px; font-family: "Ubuntu", sans-serif; font-weight: 500; font-size: 18px; color: var(--white); white-space: nowrap; }
  .issue-list { position: absolute; left: 31px; top: 75px; list-style: none; }
  .issue-list li { font-size: 14px; color: var(--white); height: 29.4px; white-space: nowrap; }

  .content-panel {
    position: absolute; left: 301px; top: 661px; width: 857px; height: 520px;
    background: var(--white); box-shadow: 4px 0 4px -2px rgba(0,0,0,.2);
  }
  .welcome-title { position: absolute; left: 35px; top: 24px; font-family: "Ubuntu", sans-serif; font-weight: 500; font-size: 31px; color: var(--pink); }
  .edit-link { position: absolute; left: 35px; top: 66px; font-size: 14px; color: #c766c0; }
  .edit-link::before { content: "•"; color: #9aa6ad; margin-right: 10px; }
  .welcome-copy { position: absolute; left: 35px; top: 96px; width: 795px; font-size: 14px; line-height: 20px; color: var(--text-grey); }
  .welcome-copy p { margin-bottom: 20px; }

  .audience-card { position: absolute; top: 996px; width: 235px; }
  .audience-card h3 { font-family: "Ubuntu", sans-serif; font-weight: 500; font-size: 18px; color: var(--pink); margin-bottom: 4px; }
  .audience-photo { width: 235px; height: 150px; }
  .card-kids { left: 325px; }
  .card-kids .audience-photo { background: linear-gradient(135deg, #e7e1da, #b9a99a); }
  .card-tweens { left: 601px; }
  .card-tweens .audience-photo { background: linear-gradient(135deg, #a58bc4, #6a4a3c); }
  .card-teens { left: 877px; }
  .card-teens .audience-photo { background: linear-gradient(135deg, #d8b48a, #5c4a40); }
</style>
</head>
<body>

<header>
  <div class="utility-bar">
    <nav class="utility-links"><a>Home</a><a>FAQs</a><a>Contact</a></nav>
    <div class="social-square"></div>
    <div class="search-field">Search...</div>
    <div class="search-button">
      <svg width="28" height="28" viewBox="0 0 28 28"><circle cx="12" cy="12" r="6.5" fill="none" stroke="#fff" stroke-width="3"/><line x1="17" y1="17" x2="23" y2="23" stroke="#fff" stroke-width="4" stroke-linecap="round"/></svg>
    </div>
  </div>

  <div class="brand">
    <div class="brand-circle"></div>
    <div class="brand-name">NETWISE</div>
    <div class="brand-tagline">BERMUDA ONLINE SAFETY AND SECURITY</div>
  </div>

  <div class="report-box">
    <div class="report-title">REPORT A CYBERCRIME</div>
    <div class="report-click">CLICK HERE</div>
    <div class="report-phone">or call 1-555-010-2468</div>
    <svg class="report-shield" width="84" height="96" viewBox="0 0 84 96">
      <path d="M42 4 L78 16 V46 C78 70 62 86 42 94 C22 86 6 70 6 46 V16 Z" fill="#2f7fd0" stroke="#cfd8e0" stroke-width="5"/>
    </svg>
  </div>

  <nav class="main-nav">
    <ul>
      <li class="nav-home current">HOME</li>
      <li class="nav-about">ABOUT</li>
      <li class="nav-parents">FOR PARENTS</li>
      <li class="nav-teens">FOR TEENS</li>
      <li class="nav-tweens">FOR TWEENS</li>
      <li class="nav-kids">FOR KIDS</li>
      <li class="nav-teachers">FOR TEACHERS</li>
      <li class="nav-resources">RESOURCES</li>
    </ul>
  </nav>
</header>

<section class="hero">
  <div class="hero-photo" role="img" aria-label="Photo of an upset girl at a desk with a laptop and phone"></div>
  <div class="hero-character" role="img" aria-label="Cartoon lizard mascot giving an OK sign"></div>
  <div class="hero-title">CYBERBULLYING</div>
</section>

<aside class="issue-sidebar">
  <div class="issue-frame"></div>
  <div class="issue-heading">CHOOSE AN ISSUE</div>
  <ul class="issue-list">
    <li>Cyberbullying</li><li>Sexting</li><li>Internet Safety</li><li>Fraud</li>
    <li>Mobile Devices</li><li>Gangs</li><li>Blogging</li><li>Predators</li>
    <li>Copywriting</li><li>Social Networking</li><li>Gaming</li>
    <li>eMailing, Chat Rooms</li><li>File Sharing</li><li>Identity Theft</li>
  </ul>
</aside>

<main class="content-panel">
  <h1 class="welcome-title">WELCOME</h1>
  <div class="edit-link">Edit</div>
  <div class="welcome-copy">
    <p>Welcome to Netwise, Bermuda’s source of information on internet safety, brought to you by the Office of Digital Affairs. Our aim is to provide practical tips, resources and contact information to help parents, children and educators to use the Internet safely and be on guard against online predators and other inappropriate online content.</p>
    <p>By knowing the dangers and how to avoid them, you can take advantage of all the positive aspects of the Internet while avoiding most of its pitfalls.</p>
    <p>The Office of Digital Affairs partners with the Island Constabulary, Northgate Software, Pixel Pals World and a number of other organizations locally and internationally to bring innovative and media rich educational tools to Bermuda</p>
  </div>
</main>

<article class="audience-card card-kids">
  <h3>KIDS</h3>
  <div class="audience-photo" role="img" aria-label="Photo of a young child using a tablet"></div>
</article>
<article class="audience-card card-tweens">
  <h3>TWEENS</h3>
  <div class="audience-photo" role="img" aria-label="Photo of a tween girl at a computer"></div>
</article>
<article class="audience-card card-teens">
  <h3>TEENS</h3>
  <div class="audience-photo" role="img" aria-label="Photo of teenagers working at computers in a classroom"></div>
</article>

</body>
</html>
```